product development company BRVEMKO LLC business card

We need a business card design for a company based in Texas called 'BRVEMKO LLC'. Our first product is a illuminated portable ice chest that is called ' Copper Harbor coolers'. Copper harbor coolers is trademarked. I would like to have the copper harbor trademark somewhere on the card as well as the BRVEMKO LLC name.

Target Market(s)

outdoor industry

Industry/Entity Type

Business

Contact Information for Business Card

i would like to have BRVEMKO LLC logo larger than the Copper harbor coolers logo.

Font styles to use
Serif
Sans Serif

```html
<!DOCTYPE html>
<html lang="en">
<head>
<meta charset="utf-8">
<title>BRVEMKO LLC business card</title>
<link href="https://fonts.googleapis.com/css2?family=Cinzel:wght@600;700&family=Tinos:wght@400;700&display=swap" rel="stylesheet">
<style>
  :root {
    --backdrop: #2a2a2a;
    --card-dark: #231f20;
    --card-light: #ffffff;
    --ink-light: #ffffff;
    --ink-dark: #111111;
    --ink-muted: #8a8a8a;
    --icon-bg: #9a9a9a;
  }
  * { margin: 0; padding: 0; box-sizing: border-box; }
  html, body { width: 1189px; height: 1200px; overflow: hidden; }
  body { background: var(--backdrop); position: relative; font-family: "Tinos", "Times New Roman", serif; }

  .card { position: absolute; left: 172px; width: 854px; height: 487px; box-shadow: 0 6px 18px rgba(0,0,0,.55); }
  .card--front { top: 68px; background: var(--card-dark); color: var(--ink-light); }
  .card--back { top: 627px; background: var(--card-light); color: var(--ink-dark); }

  .wordmark { position: absolute; font-family: "Cinzel", serif; font-weight: 700; text-align: center; }
  .wordmark__name { display: block; letter-spacing: 4px; line-height: 1; }
  .wordmark__suffix { display: flex; align-items: center; justify-content: center; gap: 12px; font-weight: 600; letter-spacing: 10px; line-height: 1; }
  .wordmark__dots { letter-spacing: 4px; font-weight: 700; }

  .card--front .wordmark { left: 0; right: 0; top: 170px; }
  .card--front .wordmark__name { font-size: 72px; }
  .card--front .wordmark__suffix { font-size: 38px; margin-top: 8px; }
  .card--front .wordmark__dots { font-size: 20px; }

  .card--back .wordmark { left: 42px; top: 58px; width: 410px; }
  .card--back .wordmark__name { font-size: 54px; letter-spacing: 3px; }
  .card--back .wordmark__suffix { font-size: 30px; margin-top: 6px; }
  .card--back .wordmark__dots { font-size: 16px; }

  .product-mark { position: absolute; display: flex; align-items: center; gap: 10px; font-family: "Cinzel", serif; font-weight: 700; font-size: 20px; line-height: 1.05; }
  .product-mark__dot { width: 30px; height: 30px; border-radius: 50%; flex: none; }
  .card--front .product-mark { left: 330px; top: 390px; color: var(--ink-light); }
  .card--front .product-mark__dot { background: var(--ink-light); }
  .card--back .product-mark { left: 512px; top: 380px; color: var(--ink-dark); }
  .card--back .product-mark__dot { background: var(--ink-dark); }

  .person { position: absolute; left: 42px; top: 216px; }
  .person__name { font-size: 25px; font-weight: 400; letter-spacing: .5px; line-height: 1; }
  .person__role { font-size: 19px; color: var(--ink-muted); line-height: 1.05; }

  .address { position: absolute; left: 42px; top: 298px; font-size: 21px; line-height: 29px; font-style: normal; }

  .contacts { position: absolute; left: 42px; top: 373px; list-style: none; font-size: 20px; }
  .contacts li { display: flex; align-items: center; gap: 8px; height: 26.5px; }
  .contacts svg { width: 22px; height: 22px; flex: none; }
</style>
</head>
<body>
  <section class="card card--front" aria-label="Card front">
    <div class="wordmark">
      <span class="wordmark__name">BRVEMKO</span>
      <span class="wordmark__suffix"><span class="wordmark__dots">·······</span>LLC<span class="wordmark__dots">·······</span></span>
    </div>
    <div class="product-mark"><span class="product-mark__dot"></span><span>Copper Harbor<br>coolers</span></div>
  </section>

  <section class="card card--back" aria-label="Card back">
    <div class="wordmark">
      <span class="wordmark__name">BRVEMKO</span>
      <span class="wordmark__suffix"><span class="wordmark__dots">·······</span>LLC<span class="wordmark__dots">·······</span></span>
    </div>
    <div class="person">
      <p class="person__name">DARA WELLS</p>
      <p class="person__role">Maneger</p>
    </div>
    <address class="address">Your Address,2nd Ste<br>Millbrook, Texas 1234</address>
    <ul class="contacts">
      <li><svg viewBox="0 0 22 22" aria-hidden="true"><rect width="22" height="22" fill="var(--icon-bg)"/><path d="M6 8c0-1.5 1.5-2.5 5-2.5s5 1 5 2.5v1h-2.5V8h-5v1H6z M7 10h8l1 6H6z" fill="#fff"/></svg>123 456 7890</li>
      <li><svg viewBox="0 0 22 22" aria-hidden="true"><rect width="22" height="22" fill="var(--icon-bg)"/><rect x="4.5" y="6.5" width="13" height="9" fill="none" stroke="#fff" stroke-width="1.4"/><path d="M4.5 6.5l6.5 5 6.5-5" fill="none" stroke="#fff" stroke-width="1.4"/></svg>your@yourcompany.com</li>
      <li><svg viewBox="0 0 22 22" aria-hidden="true"><rect width="22" height="22" fill="var(--icon-bg)"/><g fill="none" stroke="#fff" stroke-width="1.2"><circle cx="11" cy="11" r="6.5"/><ellipse cx="11" cy="11" rx="3" ry="6.5"/><path d="M4.5 11h13M5.5 8h11M5.5 14h11"/></g></svg>www.yourcompany.com</li>
    </ul>
    <div class="product-mark"><span class="product-mark__dot"></span><span>Copper Harbor<br>coolers</span></div>
  </section>
</body>
</html>
```